Chicago Train Advertisement for RideNestHomes.com.

We have purchased one month of advertising on the Chicago RLX subway train. We will have 150 cards up in the subway to advertise our website RideNestHomes.com where people can search for properties by train station. The cards are 11" tall and 46.5" long. We want people to feel compelled to jump on their cell phones and conduct a search for an apartment or home while they are riding the train, or at least enter their email and search criteria so one of our agents can help them.

Target Market(s)

People who want to live near train stations

Industry/Entity Type

Real Estate

Font styles to use
Sans Serif

Colors

Designer to choose colors to be used in the design.

Requirements
Must have
• The ridenesthomes logo and a catchy slogan, something like: Find your home near a train station the easy way: www.ridenesthome.com. Search real estate listings near the RLX or Valox.

```html
<!DOCTYPE html>
<html lang="en">
<head>
<meta charset="utf-8">
<title>RideNestHomes.com – Transit Card</title>
<link rel="stylesheet" href="https://fonts.googleapis.com/css2?family=Montserrat:ital,wght@0,300;0,400;0,500;0,700;1,700&display=swap">
<style>
  :root {
    --navy: #1c1b50;
    --sky: #2aa3de;
    --ink: #2b2b2b;
    --paper: #ffffff;
    --divider: #24234f;
    --haze: #f3f3f3;
    --city-light: #c4c4c4;
    --city-mid: #a3a3a3;
    --city-dark: #7e7e7e;
    --shore: #e6e6e6;
    --lake: #c2c2c4;
    --lake-deep: #b3b3b6;
    --url-ink: #3a3a4a;
  }
  * { box-sizing: border-box; margin: 0; padding: 0; }
  html, body { width: 1200px; height: 284px; overflow: hidden; background: var(--paper); }
  .transit-card {
    position: relative;
    width: 1200px;
    height: 284px;
    background: var(--paper);
    font-family: "Montserrat", sans-serif;
  }
  .brand {
    position: absolute;
    left: 34px;
    top: 70px;
    display: flex;
    align-items: center;
    gap: 16px;
  }
  .brand-dot {
    width: 40px;
    height: 40px;
    border-radius: 50%;
    background: var(--sky);
  }
  .brand-name {
    font-size: 46px;
    font-weight: 500;
    color: var(--navy);
    letter-spacing: -0.6px;
    line-height: 1;
  }
  .slogan {
    position: absolute;
    left: 214px;
    top: 124px;
    font-size: 21px;
    font-weight: 300;
    color: var(--ink);
    line-height: 33px;
    letter-spacing: 0.3px;
  }
  .slogan strong { color: var(--sky); font-weight: 700; }
  .slogan em { color: var(--sky); font-weight: 700; font-style: italic; }
  .divider {
    position: absolute;
    left: 598px;
    top: 0;
    width: 5px;
    height: 284px;
    background: var(--divider);
  }
  .skyline {
    position: absolute;
    left: 603px;
    top: 0;
    width: 597px;
    height: 284px;
    background:
      radial-gradient(ellipse 30% 45% at 80% 42%, rgba(90,90,90,0.35), rgba(90,90,90,0) 70%),
      radial-gradient(ellipse 45% 35% at 30% 55%, rgba(110,110,110,0.3), rgba(110,110,110,0) 70%),
      linear-gradient(180deg,
        var(--haze) 0%,
        var(--haze) 10%,
        var(--city-light) 26%,
        var(--city-mid) 50%,
        var(--city-dark) 68%,
        var(--city-mid) 72%,
        var(--shore) 75%,
        var(--shore) 77%,
        var(--lake) 82%,
        var(--lake-deep) 100%);
  }
  .site-address {
    position: absolute;
    left: 603px;
    width: 597px;
    top: 248px;
    text-align: center;
    font-size: 17px;
    font-weight: 400;
    letter-spacing: 4.4px;
    color: var(--url-ink);
  }
  .site-address .accent { color: var(--sky); font-weight: 500; }
</style>
</head>
<body>
  <main class="transit-card">
    <div class="brand">
      <span class="brand-dot" aria-hidden="true"></span>
      <span class="brand-name">RideNestHomes.com</span>
    </div>
    <p class="slogan">
      Find <strong>Great</strong><br>
      <strong>Housing</strong> near<br>
      Train Stations<br>
      the <em>Easy</em> Way!
    </p>
    <div class="divider" aria-hidden="true"></div>
    <div class="skyline" role="img" aria-label="Black and white aerial photograph of the Chicago skyline with tall towers above the lakefront and the lake in the foreground"></div>
    <p class="site-address">www.<span class="accent">ridenesthomes</span>.com</p>
  </main>
</body>
</html>
```